A5 Flyer for Financial Services Business

I am after a re-design of our business flyer to fit in with our new branding style and logo colour scheme. Wanting something with a bit of designer flair that I could not create myself. I have included the flyer which I created which lacks style so dazzle me.

I want to use the same content.

Text for main body of flyer is

Are you a small business owner, tradie or TRPQ Service Provider struggling to stay on top of your bookkeeping and compliance obligations? If so we would love to help you get back on track and take control of your business finances so that you can make informed business decisions and focus on what you do best.

We have over 20 years industry experience and, as a small business ourselves, we are able to offer our clients a personal bookkeeping solution tailored to meet the needs of your business.

Accounts Payable | Accounts Receivable
Customer Invoicing
Bank and Credit Card Reconciliations
Payroll | Superannuation | Payroll Tax
Business Activity | Instalment Activity Statements
Regular Financial Reports
Vantly and Brimfolk Set-Up and Training

```html
<!DOCTYPE html>
<html lang="en">
<head>
<meta charset="utf-8">
<title>Steady Ledger Financial Services – Bookkeeping Flyer</title>
<link href="https://fonts.googleapis.com/css2?family=Heebo:wght@300;400;700;800&family=Montserrat:wght@400;500;600;700&display=swap" rel="stylesheet">
<style>
  :root {
    --teal: #0f7f96;
    --teal-bright: #1596bb;
    --teal-deep: #0b6d82;
    --navy: #0d4a6b;
    --ink: #1c2735;
    --page: #e9eaec;
    --white: #ffffff;
    --grey-rule: #c9ced4;
    --badge-grey: #d7dce1;
  }
  * { margin: 0; padding: 0; box-sizing: border-box; }
  html, body { width: 901px; height: 1200px; overflow: hidden; background: var(--page); }
  .stage { position: relative; width: 901px; height: 1200px; }
  .flyer {
    position: absolute; left: 32.5px; top: 7.5px;
    width: 730px; height: 1035px;
    transform: scale(1.145); transform-origin: 0 0;
    background: var(--white);
    overflow: hidden;
    box-shadow: 0 6px 18px rgba(0,0,0,.18);
    font-family: "Montserrat", sans-serif;
  }
  .flyer-art { position: absolute; inset: 0; }
  .brand { position: absolute; left: 47px; top: 24px; width: 260px; text-align: center; color: var(--teal); font-family: "Heebo", sans-serif; font-weight: 300; }
  .brand-mark { width: 62px; height: 62px; border-radius: 50%; background: var(--teal); margin: 0 auto 10px; }
  .brand-name { font-size: 29px; line-height: 1; letter-spacing: -0.5px; }
  .brand-sub { font-size: 15px; letter-spacing: 6.3px; margin-top: 2px; }
  .headline { position: absolute; left: 48px; top: 178px; color: var(--white); font-family: "Heebo", sans-serif; font-size: 31px; line-height: 37.5px; }
  .headline strong { font-weight: 700; }
  .headline span { font-weight: 300; }
  .headline-rule { position: absolute; left: 50px; top: 342px; width: 250px; height: 2px; background: rgba(255,255,255,.35); }
  .headline-rule::before { content: ""; position: absolute; left: 0; top: 0; width: 130px; height: 2px; background: var(--white); }
  .years { position: absolute; left: 50px; top: 366px; display: flex; align-items: baseline; gap: 8px; color: var(--white); }
  .years-number { font-family: "Heebo", sans-serif; font-weight: 800; font-size: 60px; line-height: 64px; }
  .years-label { font-family: "Montserrat", sans-serif; font-weight: 700; font-size: 20px; }
  .intro { position: absolute; left: 48px; top: 450px; width: 365px; color: var(--white); font-size: 16px; line-height: 22px; font-weight: 500; }
  .intro strong { font-size: 20px; font-weight: 700; }
  .pitch { position: absolute; left: 50px; top: 584px; width: 632px; color: var(--ink); font-size: 15.6px; line-height: 22px; font-weight: 500; }
  .pitch .lead { color: var(--teal); }
  .pitch strong { color: var(--navy); font-weight: 700; font-size: 17px; }
  .section-rule { position: absolute; left: 48px; top: 710px; width: 634px; height: 2px; background: var(--grey-rule); }
  .section-rule::before { content: ""; position: absolute; left: 0; top: -1px; width: 332px; height: 4px; background: var(--teal); border-radius: 2px; }
  .services { position: absolute; left: 46px; top: 736px; width: 680px; list-style: none; display: grid; grid-template-columns: 364px 310px; row-gap: 19px; }
  .service { display: flex; align-items: center; gap: 26px; color: var(--ink); font-size: 15.6px; line-height: 19px; font-weight: 500; height: 38px; white-space: nowrap; }
  .service-num { flex: 0 0 32px; width: 32px; height: 34px; }
  .accreditation { position: absolute; left: 52px; top: 913px; display: flex; align-items: center; gap: 20px; }
  .accreditation-badge { width: 86px; height: 86px; border-radius: 50%; background: var(--badge-grey); }
  .accreditation-text { font-family: "Heebo", sans-serif; font-weight: 300; font-size: 19px; line-height: 22px; color: var(--ink); }
  .contact { position: absolute; left: 318px; top: 940px; color: var(--white); }
  .contact-phone { display: flex; align-items: center; gap: 12px; font-size: 23px; font-weight: 700; margin-bottom: 6px; }
  .contact-line { display: flex; align-items: center; gap: 14px; font-size: 14.5px; font-weight: 500; line-height: 23px; }
  .contact svg { flex: 0 0 auto; }
</style>
</head>
<body>
<div class="stage">
  <div class="flyer">
    <svg class="flyer-art" viewBox="0 0 730 1035" width="730" height="1035">
      <defs>
        <linearGradient id="panelGrad" x1="0" y1="0" x2="1" y2="1">
          <stop offset="0" stop-color="#0d7990"/>
          <stop offset="1" stop-color="#1aa0c6"/>
        </linearGradient>
        <linearGradient id="photoGrad" x1="0" y1="0" x2="1" y2="1">
          <stop offset="0" stop-color="#c9d3da"/>
          <stop offset=".5" stop-color="#eef0f2"/>
          <stop offset="1" stop-color="#dfe3e6"/>
        </linearGradient>
        <linearGradient id="contactGrad" x1="0" y1="0" x2="1" y2="0">
          <stop offset="0" stop-color="#0b4f72"/>
          <stop offset="1" stop-color="#0e7d92"/>
        </linearGradient>
      </defs>
      <path class="hero-panel" d="M0 163 H400 L560 560 H0 Z" fill="url(#panelGrad)"/>
      <path class="photo-frame-outer" d="M495 -20 L385 160 C368 188 368 212 385 240 L555 485 C568 500 580 505 600 505 L760 505" fill="none" stroke="var(--navy)" stroke-width="64" stroke-linejoin="round"/>
      <path class="photo-frame-gap" d="M495 -20 L385 160 C368 188 368 212 385 240 L555 485 C568 500 580 505 600 505 L760 505" fill="none" stroke="var(--white)" stroke-width="22" stroke-linejoin="round"/>
      <path class="hero-photo" role="img" aria-label="Photo of a hand writing on financial paperwork beside a calculator and laptop" d="M495 0 L385 160 C368 188 368 212 385 240 L555 485 C568 500 580 505 600 505 L730 505 L730 0 Z" fill="url(#photoGrad)"/>
      <path class="contact-panel" d="M330 930 H730 V1035 H275 V985 C275 950 295 930 330 930 Z" fill="url(#contactGrad)"/>
      <rect class="footer-strip" x="0" y="1010" width="290" height="25" fill="var(--teal)"/>
    </svg>

    <div class="brand">
      <div class="brand-mark"></div>
      <div class="brand-name">STEADY LEDGER</div>
      <div class="brand-sub">Financial Services</div>
    </div>

    <h1 class="headline">
      <strong>Affordable</strong><br>
      <strong>Bookkeeping</strong><br>
      <strong>Tailored</strong> <span>to your</span><br>
      <span>Business needs</span>
    </h1>
    <div class="headline-rule"></div>

    <div class="years">
      <span class="years-number">20</span>
      <span class="years-label">years</span>
    </div>

    <p class="intro"><strong>Industry experience</strong> and, as a small business ourselves, we are able to offer our clients a personal bookkeeping solution tailored to meet the needs of your business.</p>

    <p class="pitch"><span class="lead">Are you a small business owner, </span><strong>tradie or TRPQ Service</strong> Provider struggling to stay on top of your bookkeeping and compliance obligations? If so we would love to help you get back on track and take control of your business finances so that you can make informed business decisions and focus on what you do best.</p>

    <div class="section-rule"></div>

    <ul class="services">
      <li class="service"><svg class="service-num" viewBox="0 0 32 34"><polygon points="16,1 30,9 30,25 16,33 2,25 2,9" fill="#1aa3d6" stroke="#0b6d82" stroke-width="2"/><text x="16" y="22" text-anchor="middle" font-family="Montserrat, sans-serif" font-weight="700" font-size="13" fill="#fff">1</text></svg><span>Business Activity |<br>Instalment Activity Statements</span></li>
      <li class="service"><svg class="service-num" viewBox="0 0 32 34"><polygon points="16,1 30,9 30,25 16,33 2,25 2,9" fill="#1aa3d6" stroke="#0b6d82" stroke-width="2"/><text x="16" y="22" text-anchor="middle" font-family="Montserrat, sans-serif" font-weight="700" font-size="13" fill="#fff">2</text></svg><span>Vantly and Brimfolk Set-Up<br>and Training</span></li>
      <li class="service"><svg class="service-num" viewBox="0 0 32 34"><polygon points="16,1 30,9 30,25 16,33 2,25 2,9" fill="#1aa3d6" stroke="#0b6d82" stroke-width="2"/><text x="16" y="22" text-anchor="middle" font-family="Montserrat, sans-serif" font-weight="700" font-size="13" fill="#fff">3</text></svg><span>Bank and Credit Card<br>Reconciliations</span></li>
      <li class="service"><svg class="service-num" viewBox="0 0 32 34"><polygon points="16,1 30,9 30,25 16,33 2,25 2,9" fill="#1aa3d6" stroke="#0b6d82" stroke-width="2"/><text x="16" y="22" text-anchor="middle" font-family="Montserrat, sans-serif" font-weight="700" font-size="13" fill="#fff">4</text></svg><span>Payroll | Superannuation |<br>Payroll Tax</span></li>
      <li class="service"><svg class="service-num" viewBox="0 0 32 34"><polygon points="16,1 30,9 30,25 16,33 2,25 2,9" fill="#1aa3d6" stroke="#0b6d82" stroke-width="2"/><text x="16" y="22" text-anchor="middle" font-family="Montserrat, sans-serif" font-weight="700" font-size="13" fill="#fff">5</text></svg><span>Accounts Payable |<br>Accounts Receivable</span></li>
      <li class="service"><svg class="service-num" viewBox="0 0 32 34"><polygon points="16,1 30,9 30,25 16,33 2,25 2,9" fill="#1aa3d6" stroke="#0b6d82" stroke-width="2"/><text x="16" y="22" text-anchor="middle" font-family="Montserrat, sans-serif" font-weight="700" font-size="13" fill="#fff">6</text></svg><span>Regular Financial Reports I<br>Customer Invoicing</span></li>
    </ul>

    <div class="accreditation">
      <div class="accreditation-badge" role="img" aria-label="Registration badge"></div>
      <p class="accreditation-text">BAS Agent<br>24810937</p>
    </div>

    <div class="contact">
      <div class="contact-phone">
        <svg width="18" height="18" viewBox="0 0 24 24"><path d="M6.6 10.8a15.1 15.1 0 0 0 6.6 6.6l2.2-2.2a1 1 0 0 1 1-.25 11.4 11.4 0 0 0 3.6.57 1 1 0 0 1 1 1V20a1 1 0 0 1-1 1A17 17 0 0 1 3 4a1 1 0 0 1 1-1h3.5a1 1 0 0 1 1 1c0 1.25.2 2.45.57 3.6a1 1 0 0 1-.25 1z" fill="#fff"/></svg>
        <span>1300 555 214</span>
      </div>
      <div class="contact-line">
        <svg width="13" height="13" viewBox="0 0 24 24"><circle cx="12" cy="12" r="10" fill="none" stroke="#fff" stroke-width="2"/><path d="M2 12h20M12 2c3 3 3 17 0 20M12 2c-3 3-3 17 0 20" fill="none" stroke="#fff" stroke-width="1.6"/></svg>
        <span>steadyledgerfinancial.com</span>
      </div>
      <div class="contact-line">
        <svg width="13" height="13" viewBox="0 0 24 24"><rect x="2" y="5" width="20" height="14" fill="#fff"/><path d="M2 5l10 8 10-8" fill="none" stroke="#0b5a78" stroke-width="2"/></svg>
        <span>hello@steadyledgerfinancial.com.au</span>
      </div>
    </div>
  </div>
</div>
</body>
</html>
```